SOLVE Study flyer

I need help designing a flyer for a research study that will include brain imaging in adolescents. The info is in the attached document. The study is called the Sequoia Outlook Lantern Valley Echo (SOLVE) study. Ideally this would be returned as a document that I can edit in the future as we will have several new recruitment phases (different age groups, etc. I also would love to have a logo designed as part of this project, but I recognize that might be a separate design request.

```html
<!DOCTYPE html>
<html lang="en">
<head>
<meta charset="utf-8">
<title>SOLVE Study Flyer</title>
<link rel="stylesheet" href="https://fonts.googleapis.com/css2?family=Montserrat:wght@400;500;600;700;800;900&display=swap">
<style>
:root{
  --navy:#0d1f54;
  --purple:#7d4fb3;
  --purple-mid:#8b6cc1;
  --violet:#8e44ad;
  --lavender:#f4f1f8;
  --yellow:#f3bb1c;
  --ink:#111;
  --grey:#555;
  --white:#fff;
}
*{margin:0;padding:0;box-sizing:border-box}
html,body{width:927px;height:1200px;overflow:hidden;background:var(--white)}
body{font-family:"Montserrat",sans-serif;color:var(--ink)}
.flyer{position:relative;width:927px;height:1200px;overflow:hidden;background:var(--white)}
.abs{position:absolute}

.hero-photo{position:absolute;left:0;top:0;width:927px;height:410px}

.wordmark{left:42px;top:34px;font-size:111px;font-weight:900;letter-spacing:-2px;line-height:1;
  background:linear-gradient(90deg,var(--navy) 0%,#4a2d8f 45%,var(--violet) 75%);
  -webkit-background-clip:text;background-clip:text;color:transparent}
.study-name{left:44px;top:163px;font-size:21.5px;font-weight:800;color:var(--navy);line-height:30px;letter-spacing:.3px}
.question{left:45px;top:244px;font-size:29px;font-weight:500;line-height:38px}
.question .age{color:var(--yellow);font-weight:800}
.lead{left:44px;top:338px;font-size:20px;font-weight:400}
.lead b{color:var(--purple);font-weight:800}
.lead b.or{color:var(--navy)}

.band{left:0;top:410px;width:927px;height:100px;background:var(--navy)}
.band-icon{left:46px;top:437px;width:58px;height:58px;border:3px solid var(--white);border-radius:50%}
.band-text{left:122px;top:438px;width:790px;font-size:15px;font-weight:700;color:var(--white);line-height:26px}
.band-text .age{color:var(--yellow);font-size:19px}

.card{top:555px;width:361px;height:445px;background:var(--lavender);border-radius:8px}
.card-left{left:40px}
.card-right{left:431px}
.tab{top:555px;height:39px;border-radius:6px;color:var(--white);font-size:15px;font-weight:700;display:flex;align-items:center;padding-left:15px;letter-spacing:.2px}
.tab-purple{left:44px;width:315px;background:var(--purple-mid)}
.tab-navy{left:434px;width:355px;background:var(--navy);padding-left:18px}

.step-icon{left:56px;width:71px;height:71px;border-radius:50%;background:var(--purple-mid)}
.step-title{left:145px;font-size:17px;font-weight:700}
.step-title em{font-style:normal;color:var(--purple-mid)}
.step-body{left:146px;width:230px;font-size:15px;color:var(--grey);line-height:20.4px}

.check{left:455px;width:28px;height:28px;border-radius:50%;background:var(--purple)}
.crit{left:500px;font-size:17px;line-height:23px;width:260px}
.crit b{color:var(--purple);font-weight:700}

.art-head{left:724px;top:688px;width:192px;height:324px;border-radius:50% 50% 10% 10%/35% 35% 0 0;
  background:radial-gradient(circle at 55% 30%,#b679d6,#8e3fbf 70%)}
.art-child{left:590px;top:844px;width:125px;height:168px;border-radius:50% 50% 10% 10%/40% 40% 0 0;
  background:linear-gradient(160deg,#f6b6e6,#b9c8f5 45%,#9fe3d8 70%,#f7d6b0)}

.footer{left:0;top:1012px;width:927px;height:188px;background:var(--navy)}
.mail-icon{left:46px;top:1056px;width:84px;height:84px;border-radius:50%;background:var(--yellow)}
.cta{left:151px;top:1052px;font-size:21.5px;font-weight:600;color:var(--white);line-height:29px;letter-spacing:.5px}
.cta .hi{color:var(--yellow);font-weight:700}
.email{left:156px;top:1148px;font-size:22px;font-weight:700;color:var(--white)}
.divider{left:541px;top:1040px;width:2px;height:146px;background:var(--white)}
.gift-icon{left:577px;top:1066px;width:83px;height:83px;border:3px solid var(--white);border-radius:50%}
.comp{left:676px;top:1074px;font-size:22px;font-weight:500;color:var(--white);letter-spacing:.5px}
.upto{left:680px;top:1110px;font-size:22px;font-weight:500;color:var(--white)}
.amount{left:748px;top:1096px;font-size:56px;font-weight:900;color:var(--yellow);letter-spacing:-1px}
</style>
</head>
<body>
<div class="flyer">

  <svg class="hero-photo" viewBox="0 0 927 410" aria-hidden="false">
    <defs>
      <clipPath id="heroClip"><circle cx="866" cy="160" r="345"/></clipPath>
      <linearGradient id="heroTone" x1="0" y1="0" x2="1" y2="1">
        <stop offset="0" stop-color="#8d8494"/>
        <stop offset=".5" stop-color="#c9b3a6"/>
        <stop offset="1" stop-color="#5b6f92"/>
      </linearGradient>
    </defs>
    <circle cx="866" cy="160" r="348" fill="none" stroke="#8b6cc1" stroke-width="5"/>
    <rect role="img" aria-label="Photo of four teenage girls walking together outside a school" x="0" y="0" width="927" height="410" fill="url(#heroTone)" clip-path="url(#heroClip)"/>
  </svg>

  <div class="abs wordmark">SOLVE</div>
  <div class="abs study-name">SEQUOIA OUTLOOK LANTERN<br>VALLEY ECHO STUDY</div>
  <div class="abs question">Are you the parent of a child<br><span class="age">age 10-17?</span></div>
  <div class="abs lead">Do they <b>worry</b> <b class="or">or</b> <b>overthink</b> negative emotions?</div>

  <div class="abs band"></div>
  <div class="abs band-icon">
    <svg viewBox="0 0 52 52" width="52" height="52" fill="none" stroke="#fff" stroke-width="1.8">
      <path d="M26 13c-3-3-9-2-10 2-4 0-6 4-4 7-3 2-2 7 1 8 0 4 4 6 7 5 2 3 6 3 6 0z"/>
      <path d="M26 13c3-3 9-2 10 2 4 0 6 4 4 7 3 2 2 7-1 8 0 4-4 6-7 5-2 3-6 3-6 0z"/>
      <path d="M26 13v22M19 20c2 1 3 3 2 5M33 20c-2 1-3 3-2 5M17 29c2 0 4 1 4 3M35 29c-2 0-4 1-4 3"/>
    </svg>
  </div>
  <div class="abs band-text">Harborview University researchers are seeking girls <span class="age">age 10-17</span> for a study about brain activity in emotions and decision-making and how they relate to puberty, anxiety and depression.</div>

  <div class="abs card card-left"></div>
  <div class="abs card card-right"></div>
  <div class="abs tab tab-purple">STUDY PARTICIPATION INVOLVES:</div>
  <div class="abs tab tab-navy">YOUR CHILD MAY BE ELIGIBLE IF THEY:</div>

  <div class="abs step-icon" style="top:615px">
    <svg viewBox="0 0 71 71" width="71" height="71" fill="none" stroke="#fff" stroke-width="1.8">
      <rect x="14" y="21" width="24" height="18" rx="2"/><path d="M20 39l-2 5 6-5"/>
      <rect x="32" y="29" width="24" height="18" rx="2" fill="#8b6cc1"/><path d="M48 47l3 5-7-5M37 35h14M37 39h14M37 43h10"/>
      <text x="23" y="35" fill="#fff" stroke="none" font-size="12" font-family="Montserrat,sans-serif">?</text>
    </svg>
  </div>
  <div class="abs step-title" style="top:620px">One <em>one-hour interview</em></div>
  <div class="abs step-body" style="top:651px">(online or in-person) where your child will discuss their thoughts</div>

  <div class="abs step-icon" style="top:729px">
    <svg viewBox="0 0 71 71" width="71" height="71" fill="none" stroke="#fff" stroke-width="1.8">
      <rect x="19" y="26" width="26" height="18" rx="1"/><path d="M15 46h34l-3 3H18z"/>
      <circle cx="27" cy="33" r="3"/><path d="M22 41c1-3 9-3 10 0"/>
      <rect x="38" y="20" width="17" height="13" rx="1" fill="#8b6cc1"/><path d="M41 24h11M41 28h8"/>
    </svg>
  </div>
  <div class="abs step-title" style="top:741px">Online <em>questionnaires</em></div>
  <div class="abs step-body" style="top:770px">(parent and child)</div>

  <div class="abs step-icon" style="top:830px">
    <svg viewBox="0 0 71 71" width="71" height="71" fill="none" stroke="#fff" stroke-width="1.8">
      <rect x="26" y="17" width="18" height="11" rx="1"/><path d="M29 21h12M29 24h8"/>
      <circle cx="21" cy="31" r="3"/><circle cx="50" cy="31" r="3"/>
      <path d="M16 48v-10c0-3 10-3 10 0v4h8M55 48v-10c0-3-10-3-10 0v4h-8M20 48v-6M51 48v-6M28 42h15M35 42v8"/>
    </svg>
  </div>
  <div class="abs step-title" style="top:841px">One <em>two-hour visit</em></div>
  <div class="abs step-body" style="top:869px">where your child will complete an MRI scan, answer questions about their puberty stage, and have a small hair sample taken to study puberty hormones</div>

  <div class="abs check" style="top:627px"><svg viewBox="0 0 28 28" width="28" height="28"><path d="M8 14l4 4 8-8" fill="none" stroke="#fff" stroke-width="3" stroke-linecap="round" stroke-linejoin="round"/></svg></div>
  <div class="abs crit" style="top:630px;left:506px">Are age <b>10-17</b></div>

  <div class="abs check" style="top:704px"><svg viewBox="0 0 28 28" width="28" height="28"><path d="M8 14l4 4 8-8" fill="none" stroke="#fff" stroke-width="3" stroke-linecap="round" stroke-linejoin="round"/></svg></div>
  <div class="abs crit" style="top:698px">Tend to <b>worry</b> or <b>overthink</b> negative thoughts</div>

  <div class="abs check" style="top:767px"><svg viewBox="0 0 28 28" width="28" height="28"><path d="M8 14l4 4 8-8" fill="none" stroke="#fff" stroke-width="3" stroke-linecap="round" stroke-linejoin="round"/></svg></div>
  <div class="abs crit" style="top:761px;width:230px">have not been diagnosed with psychosis, learning problems, or autism</div>

  <div class="abs art-child" role="img" aria-label="Watercolour illustration of a young girl's silhouette in rainbow tones"></div>
  <div class="abs art-head" role="img" aria-label="Illustration of a purple head-and-shoulders silhouette with a butterfly and heart"></div>

  <div class="abs footer"></div>
  <div class="abs mail-icon">
    <svg viewBox="0 0 84 84" width="84" height="84" fill="none" stroke="var(--navy)" stroke-width="3.5" stroke-linejoin="round">
      <rect x="19" y="26" width="46" height="32" rx="3"/><path d="M19 28l23 18 23-18M19 56l17-14M65 56L48 42"/>
    </svg>
  </div>
  <div class="abs cta"><span class="hi">INTERESTED IN PARTICIPATING?</span><br>WANT MORE INFORMATION?<br>PLEASE CONTACT US!</div>
  <div class="abs email">solvestudy@harborview.edu</div>
  <div class="abs divider"></div>
  <div class="abs gift-icon">
    <svg viewBox="0 0 77 77" width="77" height="77" fill="none" stroke="var(--yellow)" stroke-width="2.6" stroke-linejoin="round">
      <rect x="22" y="32" width="33" height="8"/><rect x="24" y="40" width="29" height="18"/>
      <path d="M38.5 32v26M38.5 32c-3-7-10-8-10-3 0 3 6 3 10 3zM38.5 32c3-7 10-8 10-3 0 3-6 3-10 3z"/>
    </svg>
  </div>
  <div class="abs comp">Compensation</div>
  <div class="abs upto">up to</div>
  <div class="abs amount">$140</div>

</div>
</body>
</html>
```